Animal Eye Clinic needs a Business card

We are a new veterinary ophthalmology practice (Ridgeline Pet Vision Care) and we need a business card designed. We only see animal eyes - we are not a regular veterinary clinic. We already have a logo. We are looking for a professional, good looking business card to hand out to our clients. We are looking for something simple but professional and contemporary. Our logo is likely the only picture/graphic that needs to be on the card.
Updates

Contact Information for Business Card

Delia Vossman, BSc, DVM, MSc, DipACVO
Veterinary Ophthalmologist

Phone: 250.418.3927
Email: ridgelinepetvisioncare@mailbox-example.net
Website: ridgelinepetvisioncare-example.net
Address: 1874 Thornbury Rd
Kelowna, BC, V1X 4M9

Colors

Designer to choose colors to be used in the design.

Requirements
Must have
• Our logo (attached)

```html
<!DOCTYPE html>
<html lang="en">
<head>
<meta charset="utf-8">
<title>Ridgeline Pet Vision Care — Business Card</title>
<link rel="stylesheet" href="https://fonts.googleapis.com/css2?family=Open+Sans:wght@400;600;700&family=Open+Sans+Condensed:wght@300;700&display=swap">
<style>
  :root {
    --teal: #0a97aa;
    --teal-deep: #077f90;
    --grey: #6f6f70;
    --ink: #4a4a4b;
    --paper: #ffffff;
    --backdrop: #e2e2e3;
  }
  * { box-sizing: border-box; margin: 0; padding: 0; }
  html, body { width: 1200px; height: 800px; overflow: hidden; }
  body {
    background: var(--backdrop);
    font-family: "Open Sans", Arial, sans-serif;
    position: relative;
  }

  .card {
    position: absolute;
    background: var(--paper);
    box-shadow: 0 6px 18px rgba(0,0,0,0.16);
    overflow: hidden;
  }

  /* Front */
  .card--front { left: 50px; top: 223px; width: 620px; height: 354px; }
  .front__band {
    position: absolute; left: 0; right: 0; bottom: 0; height: 16px;
    background: var(--teal);
  }
  .brand {
    position: absolute; left: 40px; top: 150px;
    display: flex; align-items: center; gap: 12px;
  }
  .brand__dot {
    width: 38px; height: 38px; border-radius: 50%;
    background: var(--teal);
    flex: none;
  }
  .brand__name {
    color: var(--teal);
    font-weight: 600;
    font-size: 15px;
    line-height: 1.25;
    text-transform: uppercase;
    letter-spacing: 0.04em;
  }
  .brand__name span { display: block; }
  .brand__name .spaced { letter-spacing: 0.42em; }

  .contact {
    position: absolute; left: 300px; top: 72px; width: 300px;
    color: var(--ink);
  }
  .contact__name {
    color: var(--teal);
    font-weight: 700;
    font-size: 17px;
    text-transform: uppercase;
    letter-spacing: 0.01em;
  }
  .contact__creds {
    font-family: "Open Sans Condensed", "Arial Narrow", sans-serif;
    font-weight: 700;
    font-size: 13px;
    text-transform: none;
    letter-spacing: 0;
  }
  .contact__title { color: var(--grey); font-size: 13px; margin-top: 2px; }
  .contact__address { font-size: 13px; line-height: 1.4; margin-top: 18px; }
  .contact__list { list-style: none; margin-top: 14px; font-size: 11.5px; line-height: 1.65; }
  .contact__list li { display: flex; align-items: center; gap: 7px; white-space: nowrap; }
  .contact__list svg { width: 11px; height: 11px; flex: none; fill: var(--teal); }

  /* Back */
  .card--back { left: 760px; top: 120px; width: 320px; height: 560px; }
  .back__field {
    position: absolute; inset: 0;
    background: var(--teal);
    clip-path: polygon(0 36%, 62% 0, 100% 0, 100% 0, 100% 0, 0 100%);
    clip-path: polygon(0 28%, 0 100%, 40% 100%, 62% 62%, 38% 22%);
  }
  .back__ring {
    position: absolute; left: -40px; top: 210px;
    width: 250px; height: 250px; border-radius: 50%;
    border: 14px solid var(--paper);
  }
  .back__text {
    position: absolute; right: 28px; top: 40px;
    writing-mode: vertical-rl;
    display: flex; gap: 10px;
  }
  .back__name {
    color: var(--teal);
    font-weight: 600;
    font-size: 24px;
    text-transform: uppercase;
    line-height: 1.15;
  }
  .back__name span { display: block; }
  .back__name .spaced { letter-spacing: 0.5em; }
  .back__web {
    color: var(--grey);
    font-size: 13px;
    text-transform: uppercase;
    letter-spacing: 0.02em;
    margin-top: 4px;
  }
</style>
</head>
<body>

  <section class="card card--front" aria-label="Business card front">
    <div class="brand">
      <div class="brand__dot"></div>
      <div class="brand__name">
        <span class="spaced">Ridgeline</span>
        <span>Pet Vision Care</span>
      </div>
    </div>

    <div class="contact">
      <p class="contact__name">Delia Vossman, <span class="contact__creds">BSc, DVM, MSc, DipACVO</span></p>
      <p class="contact__title">Veterinary Ophthalmologist</p>
      <p class="contact__address">1874 Thornbury Rd<br>Kelowna, BC, V1X 4M9</p>
      <ul class="contact__list">
        <li>
          <svg viewBox="0 0 24 24" aria-hidden="true"><path d="M6.6 10.8a15.1 15.1 0 0 0 6.6 6.6l2.2-2.2a1 1 0 0 1 1-.25 11.4 11.4 0 0 0 3.6.57 1 1 0 0 1 1 1V20a1 1 0 0 1-1 1A17 17 0 0 1 3 4a1 1 0 0 1 1-1h3.5a1 1 0 0 1 1 1c0 1.25.2 2.45.57 3.57a1 1 0 0 1-.25 1z"/></svg>
          250.418.3927
        </li>
        <li>
          <svg viewBox="0 0 24 24" aria-hidden="true"><path d="M2 5h20v14H2z M3.5 6.5 12 13l8.5-6.5" fill="none" stroke="#0a97aa" stroke-width="2.4"/></svg>
          ridgelinepetvisioncare@mailbox-example.net
        </li>
        <li>
          <svg viewBox="0 0 24 24" aria-hidden="true"><circle cx="12" cy="12" r="10"/></svg>
          ridgelinepetvisioncare-example.net
        </li>
      </ul>
    </div>

    <div class="front__band"></div>
  </section>

  <section class="card card--back" aria-label="Business card back">
    <div class="back__field"></div>
    <div class="back__ring"></div>
    <div class="back__text">
      <p class="back__name">
        <span class="spaced">Ridgeline</span>
        <span>Pet Vision Care</span>
      </p>
      <p class="back__web">www.ridgelinepetvisioncare-example.net</p>
    </div>
  </section>

</body>
</html>
```